Business Card Design for Occupational Medicine Start Up Company

We need to design a professional business card. We are a healthcare company providing occupational medicine services to blue collar industries. We are professional, efficient and high quality service providers.

Target Market(s)

Blue Collar Industry: Shipbuilding, Ports, Trucking Companies; The Executives and Safety Officers for these companies

Industry/Entity Type

Healthcare

Contact Information for Business Card

Logo, Name, Title, Email, Phone

Other font styles liked:
• Please match our Brand Guide

Requirements
Must have
• Our Company Colors and Logo

```html
<!DOCTYPE html>
<html lang="en">
<head>
<meta charset="utf-8">
<title>CrewSafe Business Card</title>
<link href="https://fonts.googleapis.com/css2?family=Montserrat:wght@700&family=Roboto:wght@400&display=swap" rel="stylesheet">
<style>
  :root {
    --stage: #1c1c1e;
    --card-black: #111113;
    --card-black-soft: #2a2a2e;
    --card-white: #ffffff;
    --navy: #2a3589;
    --sky: #2fa8e0;
    --amber: #f5a623;
    --text: #1f1f24;
  }
  * { margin: 0; padding: 0; box-sizing: border-box; }
  html, body {
    width: 1200px; height: 900px; overflow: hidden;
    background: var(--stage);
    font-family: "Roboto", Arial, sans-serif;
  }
  .sheet {
    width: 1200px; height: 900px;
    display: flex; flex-direction: column; align-items: center; justify-content: center;
    gap: 40px;
  }
  .card {
    width: 700px; height: 400px; position: relative; overflow: hidden;
    box-shadow: 0 14px 40px rgba(0,0,0,.55);
  }
  .card--back {
    background: var(--card-black);
  }
  .back-texture {
    position: absolute; inset: 0;
    background: linear-gradient(120deg, var(--card-black) 0%, var(--card-black-soft) 65%, #3a3a40 100%);
  }
  .back-mark {
    position: absolute; right: 90px; bottom: 70px;
    font-family: "Montserrat", Arial, sans-serif; font-weight: 700;
    font-size: 15px; letter-spacing: 1px; color: var(--sky);
  }
  .card--front { background: var(--card-white); }
  .front-watermark {
    position: absolute; left: 40px; top: 30px; width: 380px; height: 340px;
    border-radius: 50%;
    background: radial-gradient(circle, rgba(47,168,224,.10) 0%, rgba(42,53,137,.06) 45%, rgba(245,166,35,.04) 70%, rgba(255,255,255,0) 75%);
  }
  .brand {
    position: absolute; left: 420px; top: 110px;
    display: flex; flex-direction: column; align-items: center; gap: 14px;
  }
  .brand-dot { width: 58px; height: 58px; border-radius: 50%; background: var(--navy); }
  .brand-name {
    font-family: "Montserrat", Arial, sans-serif; font-weight: 700;
    font-size: 34px; letter-spacing: 3px; color: var(--navy);
  }
  .name-flag {
    position: absolute; left: 0; top: 218px; width: 26px; height: 44px; background: var(--navy);
  }
  .person { position: absolute; left: 60px; top: 214px; }
  .person-name {
    font-family: "Montserrat", Arial, sans-serif; font-weight: 700;
    font-size: 32px; color: var(--navy); letter-spacing: .5px;
  }
  .person-title { font-size: 16px; color: var(--text); margin-top: 2px; }
  .contacts { position: absolute; left: 60px; top: 300px; list-style: none; }
  .contacts li {
    display: flex; align-items: center; gap: 8px;
    font-size: 18px; color: var(--text); line-height: 27px;
  }
  .contacts svg { width: 14px; height: 14px; fill: var(--navy); flex: none; }
</style>
</head>
<body>
<main class="sheet">
  <section class="card card--back">
    <div class="back-texture" role="img" aria-label="Gloss pattern of repeated brand symbols on black"></div>
    <span class="back-mark">CREWSAFE</span>
  </section>

  <section class="card card--front">
    <div class="front-watermark" role="img" aria-label="Faint enlarged brand symbol watermark"></div>
    <div class="brand">
      <span class="brand-dot"></span>
      <span class="brand-name">CREWSAFE</span>
    </div>
    <span class="name-flag"></span>
    <div class="person">
      <h1 class="person-name">DANIEL HARPER</h1>
      <p class="person-title">Director</p>
    </div>
    <ul class="contacts">
      <li>
        <svg viewBox="0 0 24 24"><path d="M6.6 10.8a15 15 0 0 0 6.6 6.6l2.2-2.2c.3-.3.7-.4 1-.2 1.1.4 2.3.6 3.6.6.6 0 1 .4 1 1V20c0 .6-.4 1-1 1A17 17 0 0 1 3 4c0-.6.4-1 1-1h3.5c.6 0 1 .4 1 1 0 1.3.2 2.5.6 3.6.1.3 0 .7-.2 1z"/></svg>
        (555)014 2290
      </li>
      <li>
        <svg viewBox="0 0 24 24"><path d="M2 5h20v14H2zm2 2v.5l8 5 8-5V7l-8 5z"/></svg>
        hello@crewsafe.com
      </li>
      <li>
        <svg viewBox="0 0 24 24"><path d="M12 2a10 10 0 1 0 0 20 10 10 0 0 0 0-20zm0 2c.9 1.2 1.7 3 2 5h-4c.3-2 1.1-3.8 2-5zm-2.6.4C8.7 5.8 8.2 7.4 8 9H4.9a8 8 0 0 1 4.5-4.6zm5.2 0A8 8 0 0 1 19.1 9H16c-.2-1.6-.7-3.2-1.4-4.6zM4.3 11H8v2H4.3a8 8 0 0 1 0-2zm5.7 0h4v2h-4zm6 0h3.7a8 8 0 0 1 0 2H16zM4.9 15H8c.2 1.6.7 3.2 1.4 4.6A8 8 0 0 1 4.9 15zm5.1 0h4c-.3 2-1.1 3.8-2 5-.9-1.2-1.7-3-2-5zm6 0h3.1a8 8 0 0 1-4.5 4.6c.7-1.4 1.2-3 1.4-4.6z"/></svg>
        www.crewsafe.com
      </li>
    </ul>
  </section>
</main>
</body>
</html>
```